Fitness Centre/Personal Trainer Business Card

We need a business card design for a company based in Singapore called 'Vigor Ledger'.

We are a team of Personal Trainers and we are planning to open our new training facility.

This design will also be printed/painted on the walls in our gym.

We are a new breed of personal trainers who take fitness seriously and holistically. We do not merely train our clients to be big and muscular.

We believe in wholeness. In our opinion, fitness should include: strength, speed, flexibility, mobility, stamina & agility. These are what we train for. Of course, nutrition/diet is key.

We use fitness tools such as kettlebells, QVL, Pylometric boxes, battling ropes, clubbells, medicine balls, bulgarian bags etc - functional and non-bulky tools.

I currently have a Facebook page 'Vigor Ledger SG' which shows a logo of a kettlebell. But my business focus has since changed.

Services provided:
- Kettlebell Sport Preparation
- Calisthenics Training
- Corrective Exercises
- Sports Strength & Conditioning
- 28 days Weight Loss Program
- Myofascial Rehab Therapy
- Sports/Thai Massage

Main colors for the design should be BLACK & YELLOW. We envision a design which is able to protray the holistic view we take on fitness. Also it should somewhat appeal to the ladies and not intimidate them.

Target Market(s)

People between 18-35 years old. Students and working class alike.

Industry/Entity Type

Training

Requirements
Must have
• Name: Marcus Obadiah Lim
Fitness Coach
Corrective Exercise Specialist
M: +65 9437 2065
E: marcus@sgvigorledger-example.com

Double-sided please.
Nice to have
• "What is your vigor ledger?"

```html
<!DOCTYPE html>
<html lang="en">
<head>
<meta charset="utf-8">
<title>Vigor Ledger Business Card</title>
<link href="https://fonts.googleapis.com/css2?family=Source+Sans+3:wght@400;600;700&display=swap" rel="stylesheet">
<style>
  :root {
    --ink: #1a1a1a;
    --black: #000000;
    --yellow: #ffe100;
    --gold: #f5d20a;
    --white: #ffffff;
    --stage-light: #f2f2f2;
    --stage-dark: #9a9a9a;
    --line: #8c8c8c;
  }
  * { margin: 0; padding: 0; box-sizing: border-box; }
  html, body { width: 1200px; height: 719px; overflow: hidden; }
  body {
    font-family: "Source Sans 3", sans-serif;
    color: var(--ink);
    background: radial-gradient(ellipse at 50% 35%, var(--stage-light) 0%, #c8c8c8 55%, var(--stage-dark) 100%);
    position: relative;
  }
  .card { position: absolute; width: 538px; height: 307px; overflow: hidden; }

  /* Front */
  .card-front { left: 48px; top: 213px; background: var(--white); border: 1px solid var(--line); }
  .front-bar { position: absolute; left: 48px; width: 163px; height: 26px; }
  .front-bar-top { top: 0; background: var(--ink); }
  .front-bar-bottom { bottom: 0; background: var(--yellow); }
  .brand-mark { position: absolute; left: 48px; top: 50px; width: 163px; text-align: center; }
  .brand-dot { display: block; width: 96px; height: 96px; margin: 0 auto 14px; border-radius: 50%; background: var(--yellow); }
  .brand-name { font-size: 28px; font-weight: 700; line-height: 1; color: var(--ink); }

  .contact { position: absolute; left: 265px; top: 76px; }
  .contact-name { font-size: 19px; font-weight: 700; line-height: 1.1; }
  .contact-role { font-size: 15px; line-height: 1.25; }
  .contact-list { list-style: none; margin-top: 20px; }
  .contact-list li { font-size: 15px; line-height: 24px; display: flex; align-items: center; gap: 5px; }
  .contact-list svg { width: 12px; height: 12px; flex: none; }

  /* Back, dark */
  .card-back-dark { left: 622px; top: 39px; background: var(--black); color: var(--white); }
  .card-back-dark .brand-mark { left: 40px; top: 62px; width: 180px; }
  .card-back-dark .brand-name { color: var(--yellow); }
  .services-dark { position: absolute; left: 276px; top: 26px; }
  .services-title { font-size: 19px; font-weight: 700; color: var(--gold); margin-bottom: 12px; }
  .services-dark ul { list-style: none; }
  .services-dark li { font-size: 15.5px; line-height: 26.6px; color: var(--gold); }
  .services-dark li::before { content: "\2022"; color: var(--white); margin-right: 3px; }
  .tagline-dark { position: absolute; left: 0; right: 0; top: 262px; padding-left: 250px; text-align: center; font-size: 16px; font-weight: 700; letter-spacing: 0.8px; }

  /* Back, light */
  .card-back-light { left: 622px; top: 388px; background: var(--white); border: 1px solid var(--line); text-align: center; }
  .ghost-name { position: absolute; left: 0; right: 0; top: 110px; font-size: 58px; font-weight: 700; color: var(--yellow); opacity: 0.16; }
  .services-light { position: relative; padding-top: 70px; }
  .services-light .services-title { color: var(--ink); font-size: 20px; margin-bottom: 14px; }
  .services-light ul { list-style: none; display: flex; flex-wrap: wrap; justify-content: center; column-gap: 6px; padding: 0 20px; }
  .services-light li { font-size: 19px; line-height: 33px; }
  .services-light li::before { content: "\2022"; margin-right: 4px; }
  .tagline-light { position: absolute; left: 0; right: 0; top: 272px; font-size: 16px; font-weight: 700; letter-spacing: 0.6px; text-transform: uppercase; }
</style>
</head>
<body>

<section class="card card-front" aria-label="Business card front">
  <div class="front-bar front-bar-top"></div>
  <div class="brand-mark">
    <span class="brand-dot"></span>
    <div class="brand-name">Vigor Ledger</div>
  </div>
  <div class="front-bar front-bar-bottom"></div>

  <div class="contact">
    <h1 class="contact-name">Marcus Obadiah Lim</h1>
    <p class="contact-role">Fitness Coach</p>
    <p class="contact-role">Corrective Exercise Specialist</p>
    <ul class="contact-list">
      <li>
        <svg viewBox="0 0 12 12" aria-hidden="true"><rect x="3" y="0.5" width="6" height="11" rx="1" fill="none" stroke="#333" stroke-width="1.2"/><rect x="4.3" y="2" width="3.4" height="5" fill="#333"/></svg>
        +65 9437 2065
      </li>
      <li>
        <svg viewBox="0 0 12 12" aria-hidden="true"><rect x="0.8" y="3" width="10.4" height="7" fill="#333"/><path d="M1 3.2 6 7 11 3.2" fill="none" stroke="#fff" stroke-width="1"/></svg>
        marcus@sgvigorledger-example.com
      </li>
      <li>
        <svg viewBox="0 0 12 12" aria-hidden="true"><circle cx="6" cy="6" r="5" fill="none" stroke="#333" stroke-width="1.1"/><ellipse cx="6" cy="6" rx="2.2" ry="5" fill="none" stroke="#333" stroke-width="0.9"/><path d="M1 6h10" stroke="#333" stroke-width="0.9"/></svg>
        www.sgvigorledger-example.com
      </li>
    </ul>
  </div>
</section>

<section class="card card-back-dark" aria-label="Business card back, dark version">
  <div class="brand-mark">
    <span class="brand-dot"></span>
    <div class="brand-name">Vigor Ledger</div>
  </div>
  <div class="services-dark">
    <h2 class="services-title">Services</h2>
    <ul>
      <li>Sports Strength &amp; Conditioning</li>
      <li>Kettlebell Sport Preparation</li>
      <li>28 days Weight Loss Program</li>
      <li>Myofascial Rehab Therapy</li>
      <li>Calisthenics Training</li>
      <li>Corrective Exercises</li>
      <li>Sports/Thai Massage</li>
    </ul>
  </div>
  <p class="tagline-dark">What is your vigor ledger?</p>
</section>

<section class="card card-back-light" aria-label="Business card back, light version">
  <div class="ghost-name" aria-hidden="true">Vigor Ledger</div>
  <div class="services-light">
    <h2 class="services-title">Services</h2>
    <ul>
      <li>Sports Strength &amp; Conditioning</li>
      <li>Sports/Thai Massage</li>
      <li>Kettlebell Sport Preparation</li>
      <li>Corrective Exercises</li>
      <li>28 days Weight Loss Program</li>
      <li>Calisthenics Training</li>
      <li>Myofascial Rehab Therapy</li>
    </ul>
  </div>
  <p class="tagline-light">What is your vigor ledger?</p>
</section>

</body>
</html>
```